Brambleton Pizza Website

We are working with Brambleton Pizza and designing them a website.

Some sites to use for content/competitors and inspiration:

https://fennimores.com
https://www.bhq-eats.com
https://brightorchard.com/en-us/

Thank you for taking the time to consider designing a website for us. We are web developers based in Stockton, CA, USA. Most of our projects go through the same process. Understanding this process may help you win a project with us. We custom-code all of our websites in-house. We don’t have any requirements as to what tools you use for your design, but we prefer Figma files. For any design that we label as four-stars, we send it to the client for review. The client picks the final design they want us to use. Once we complete this process, we will continue to show additional clients all the four-star sites and purchase them later. Your designs will have multiple chances to sell. For better chances of success, we ask that you follow these guidelines.

IMAGES:
If you use any images or icons in the design, we ask that you have a link to the asset so we can purchase the image/icon. Most of the designs we submit do not have the customer’s images on them unless they have some great images. Be creative; show us the feeling you are trying to portray with your image choices. Use any royalty-free site you choose. We subscribe to Quillstone and mainly use their images, but we can purchase images outside of Quillstone.

PLEASE NOTE: we will not submit designs to clients with watermarks on the images.

FONTS:
We ask that you identify the fonts used in the design. This can be done in a message if you want. We typically use Google Fonts and Quillstone Fonts.

CONTENT:
We're always open to different content and ideas. We often submit designs with stock images so the client can see our vision. We typically take pictures after the website launch to use their images with our vision. Lorem Ipsum is fine for paragraphs, but we ask that you write the headers in correct English. We want to be able to show the vision and identify the sections of the website.

INSPIRATION:
We typically add a couple of links in the brief of websites we like to help you get started in your design.

REVISIONS:
We do not often ask for revisions of the designs unless we see something in the design that may not appeal to the client. If there are slight changes that we want to make, we do that in the development process.

FEEDBACK:
We rarely give feedback on designs during the design process. We are working on many website projects and do not have the time to provide feedback. We usually respond if your request is well thought out and asks specific questions, but a note asking “feedback, please” usually goes unanswered.

```html
<!DOCTYPE html>
<html lang="en">
<head>
<meta charset="utf-8">
<title>Brambleton Pizza</title>
<link rel="stylesheet" href="https://fonts.googleapis.com/css2?family=Poppins:wght@400;500;600;700&family=Bodoni+Moda:wght@800&display=swap">
<style>
:root{
  --red:#e8412f;
  --green:#3dae3a;
  --ink:#111111;
  --text:#2a2a2a;
  --muted:#555555;
  --white:#ffffff;
  --footer:#1d1b1a;
}
*{margin:0;padding:0;box-sizing:border-box}
html,body{width:1200px;height:4992px;overflow:hidden}
body{position:relative;font-family:'Poppins',sans-serif;color:var(--text);background:var(--white)}
.abs{position:absolute}
.pill{position:absolute;display:flex;align-items:center;justify-content:center;background:var(--red);color:var(--white);border-radius:30px;font-weight:500;text-transform:uppercase}

/* header */
.top-pill{height:32px;width:150px;font-size:12px;top:8px}
.nav-band{top:54px;left:0;width:1200px;height:37px;background:var(--ink)}
.nav-link{top:54px;height:37px;line-height:37px;color:var(--white);font-size:12px;font-weight:500}
.brand-box{left:512px;top:0;width:176px;height:150px;background:var(--white);display:flex;flex-direction:column;align-items:center;justify-content:center;z-index:3;box-shadow:0 4px 10px rgba(0,0,0,.12)}
.brand-name{font-size:22px;font-weight:700;color:var(--ink);text-align:center;line-height:1.15;text-transform:uppercase}

/* hero */
.hero{top:91px;left:0;width:1200px;height:671px;background:linear-gradient(90deg,#ffffff 0%,#f2f2f2 40%,#e6e6e6 100%)}
.hero-photo{top:91px;left:420px;width:780px;height:671px;background:radial-gradient(ellipse at 62% 50%,#c9803a 0%,#a85a26 35%,#5a3420 60%,#2a2220 80%,rgba(240,240,240,0) 100%)}
.hero-title{left:70px;top:200px;font-family:'Bodoni Moda',serif;font-weight:800;font-size:58px;line-height:66px;letter-spacing:2px;color:var(--ink);text-transform:uppercase}
.hero-title .accent{color:var(--green)}
.hero-btn{left:68px;top:505px;width:200px;height:46px;font-size:18px}
.dot{top:664px;width:10px;height:10px;border-radius:50%;background:#bdbdbd}

/* section headings */
.section-title{left:0;width:1200px;text-align:center;font-weight:600;text-transform:uppercase;color:var(--ink)}
.divider{height:3px;width:300px;left:450px;background:linear-gradient(90deg,rgba(232,65,47,0),var(--red) 30%,var(--red) 70%,rgba(232,65,47,0))}
.divider::after{content:"";position:absolute;left:142px;top:-6px;width:15px;height:15px;border-radius:50%;background:var(--red)}

/* menus */
.menu-ring{width:316px;height:316px;border-radius:50%;background:var(--white);box-shadow:0 2px 12px rgba(0,0,0,.12);display:flex;align-items:center;justify-content:center}
.menu-photo{width:284px;height:284px;border-radius:50%}
.menu-label{width:340px;text-align:center;font-size:24px;font-weight:500;text-transform:uppercase;color:var(--ink)}
.view-btn{left:496px;top:1873px;width:208px;height:52px;font-size:19px}

/* catering band */
.catering{top:2029px;left:0;width:1200px;height:519px;background:radial-gradient(ellipse at 50% 50%,#7a3b24 0%,#4a2518 55%,#2b1810 100%)}
.catering-title{left:0;width:1200px;top:2160px;text-align:center;color:var(--white);font-weight:600;font-size:66px;line-height:84px;text-transform:uppercase}
.catering-btn{left:510px;top:2385px;width:180px;height:46px;font-size:19px;background:var(--green)}

/* packages */
.pkg-photo{top:2841px;width:310px;height:275px}
.pkg-title{top:3144px;width:300px;font-size:14px;font-weight:600;line-height:20px;color:var(--ink);text-transform:uppercase}
.pkg-desc{width:300px;font-size:12.5px;line-height:20px;color:var(--text)}
.pkg-btn{top:3266px;width:112px;height:34px;font-size:12.5px}

/* testimonial */
.testi-band{top:3500px;left:252px;width:948px;height:426px;background:var(--red)}
.testi-photo{top:3395px;left:0;width:372px;height:531px;background:linear-gradient(160deg,#7a4a32 0%,#c9a488 40%,#efe8e2 75%,#dedad6 100%)}
.testi-title{left:380px;width:686px;top:3560px;text-align:center;color:var(--white);font-weight:600;font-size:48px;text-transform:uppercase}
.testi-divider{background:linear-gradient(90deg,rgba(255,255,255,0),#fff 30%,#fff 70%,rgba(255,255,255,0));left:573px}
.testi-divider::after{background:var(--white)}
.testi-text{left:470px;width:506px;top:3684px;text-align:center;color:var(--white);font-size:16px;line-height:24px}
.avatar{left:662px;top:3804px;width:66px;height:66px;border-radius:50%;background:linear-gradient(135deg,#f3f3f3,#9a9a9a);border:2px solid #fff}
.reviewer{left:744px;top:3824px;color:var(--white);font-size:11px;font-weight:600}
.stars{left:744px;top:3840px;color:#ffd21f;font-size:10px;letter-spacing:1px}

/* gallery */
.gallery-photo{top:4234px;height:307px}

/* footer */
.footer{top:4711px;left:0;width:1200px;height:281px;background:var(--footer)}
.foot-link{top:4770px;color:var(--white);font-size:12.5px;font-weight:500;text-transform:uppercase}
.foot-line{left:75px;width:1035px;height:1px;background:rgba(255,255,255,.6)}
.contact-icon{top:4848px;width:32px;height:32px;border-radius:50%;display:flex;align-items:center;justify-content:center}
.contact-text{top:4849px;color:var(--white);font-size:12.5px;line-height:16px}
.copyright{left:75px;top:4946px;color:var(--white);font-size:11px}
.social{top:4942px;width:28px;height:28px;border:1.5px solid var(--red)}
</style>
</head>
<body>

<!-- header -->
<div class="pill top-pill" style="left:186px">Today's Deal</div>
<div class="pill top-pill" style="left:874px">Delivery &amp; Pick Up</div>

<div class="abs hero"></div>
<div class="abs hero-photo" role="img" aria-label="Large pizza topped with olives, chicken, tomatoes and sauce drizzle on a dark board"></div>

<div class="abs nav-band"></div>
<span class="abs nav-link" style="left:166px">Home</span>
<span class="abs nav-link" style="left:255px">Menu</span>
<span class="abs nav-link" style="left:340px">Catering</span>
<span class="abs nav-link" style="left:744px">About Us</span>
<span class="abs nav-link" style="left:856px">Franchise</span>
<span class="abs nav-link" style="left:975px">Start Your Order</span>

<div class="abs brand-box"><div class="brand-name">Brambleton<br>Pizza</div></div>

<h1 class="abs hero-title">Home of<br>Delicious<br><span class="accent">Italian<br>Fresh Pizza</span></h1>
<div class="pill hero-btn">Order Now</div>
<span class="abs dot" style="left:88px;background:var(--red)"></span>
<span class="abs dot" style="left:111px"></span>
<span class="abs dot" style="left:134px"></span>
<span class="abs dot" style="left:157px"></span>

<!-- menus -->
<h2 class="abs section-title" style="top:872px;font-size:62px"><span style="color:var(--red)">Our</span> Menus</h2>
<div class="abs divider" style="top:975px"></div>

<div class="abs menu-ring" style="left:96px;top:1020px"><div class="menu-photo" role="img" aria-label="Fried pizza slices with potato wedges" style="background:radial-gradient(circle,#c44a2a,#8a2e1a 60%,#3a2018)"></div></div>
<div class="abs menu-ring" style="left:442px;top:1020px"><div class="menu-photo" role="img" aria-label="Roman pizza with peppers, olives and corn" style="background:radial-gradient(circle,#e0a040,#c07a2a 60%,#5a3a22)"></div></div>
<div class="abs menu-ring" style="left:786px;top:1020px"><div class="menu-photo" role="img" aria-label="Neapolitan pizza with cheese and herbs" style="background:radial-gradient(circle,#e8b556,#d08e34 60%,#8a5a2a)"></div></div>
<div class="abs menu-label" style="left:84px;top:1357px">Fried Pizza</div>
<div class="abs menu-label" style="left:428px;top:1357px">Roman Pizza</div>
<div class="abs menu-label" style="left:794px;top:1357px">Pizza Napoletana</div>

<div class="abs menu-ring" style="left:96px;top:1440px"><div class="menu-photo" role="img" aria-label="Sicilian pizza with red and yellow peppers" style="background:radial-gradient(circle,#e2b070,#b86a2c 55%,#1e1a18)"></div></div>
<div class="abs menu-ring" style="left:442px;top:1440px"><div class="menu-photo" role="img" aria-label="Pizza al taglio with mushrooms and vegetables" style="background:radial-gradient(circle,#e6b06a,#c07a36 60%,#8a5428)"></div></div>
<div class="abs menu-ring" style="left:786px;top:1440px"><div class="menu-photo" role="img" aria-label="Pizza alla pala with falling red peppers" style="background:radial-gradient(circle,#d8743a,#a84a24 55%,#3a2a24)"></div></div>
<div class="abs menu-label" style="left:90px;top:1774px">Pizza Siciliana</div>
<div class="abs menu-label" style="left:428px;top:1774px">Pizza al Taglio</div>
<div class="abs menu-label" style="left:794px;top:1774px">Pizza alla Pala</div>

<div class="pill view-btn">View All Menus</div>

<!-- catering band -->
<div class="abs catering" role="img" aria-label="Close-up of a pizza slice being lifted with stretching cheese"></div>
<h2 class="abs catering-title">Ready to Start Your<br>Catering Order?</h2>
<div class="pill catering-btn">Order Now</div>

<!-- packages -->
<h2 class="abs section-title" style="top:2626px;font-size:45px;line-height:57px">Simplify Your Catering Experience<br>With Our Selection of Curated<br>Packages Below</h2>

<div class="abs pkg-photo" style="left:91px;background:linear-gradient(135deg,#c9c4bc,#a5744a 45%,#5a3a2a)" role="img" aria-label="Two pizzas in open takeaway boxes"></div>
<div class="abs pkg-title" style="left:93px">Custom Pizza Combo<br>Package</div>
<div class="abs pkg-desc" style="left:93px;top:3199px">Includes 5 Pizzas, 1 Catering Salad, and a Sweets Tray; serves up to 12</div>
<div class="pill pkg-btn" style="left:91px">Order Now</div>

<div class="abs pkg-photo" style="left:446px;background:linear-gradient(135deg,#e8e6e2,#c8a07a 45%,#b85a34 75%,#8a5a3a)" role="img" aria-label="Pepperoni pizza in a box beside a knife and board"></div>
<div class="abs pkg-title" style="left:448px">Custom Pizza Combo<br>Package</div>
<div class="abs pkg-desc" style="left:448px;top:3199px">Includes 5 Pizzas, 1 Catering Salad, and a Sweets Tray; serves up to 12</div>
<div class="pill pkg-btn" style="left:446px">Order Now</div>

<div class="abs pkg-photo" style="left:800px;background:linear-gradient(135deg,#4a6a2a,#d8a45a 40%,#e8dccb 70%,#a06a8a)" role="img" aria-label="Large sandwiches wrapped in paper with red onion"></div>
<div class="abs pkg-title" style="left:803px">Large Sandwich Package</div>
<div class="abs pkg-desc" style="left:803px;top:3179px">An assortment of sandwiches paired with a Classic Caesar Salad. Serves up to 20.</div>
<div class="pill pkg-btn" style="left:800px">Order Now</div>

<!-- testimonial -->
<div class="abs testi-band"></div>
<div class="abs testi-photo" role="img" aria-label="Excited young woman with glasses eating a slice of pizza"></div>
<h2 class="abs testi-title">Our Testimonial</h2>
<div class="abs divider testi-divider" style="top:3643px"></div>
<p class="abs testi-text">Lorem ipsum dolor sit amet, consectetur adipiscing elit, sed do eiusmod tempor incididunt ut labore et dolore magna aliqua. Quis ipsum suspendisse ultrices gravida. Risus commodo viverra maecenas accumsan lacus vel facilisis.</p>
<svg class="abs" style="left:406px;top:3704px" width="26" height="54" viewBox="0 0 26 54"><polyline points="24,2 3,27 24,52" fill="none" stroke="#fff" stroke-width="2"/></svg>
<svg class="abs" style="left:1050px;top:3704px" width="26" height="54" viewBox="0 0 26 54"><polyline points="2,2 23,27 2,52" fill="none" stroke="#fff" stroke-width="2"/></svg>
<div class="abs avatar" role="img" aria-label="Customer portrait"></div>
<div class="abs reviewer">Marla Quince</div>
<div class="abs stars">★★★★★</div>

<!-- gallery -->
<h2 class="abs section-title" style="top:4048px;font-size:64px">Follow Us on Snapgrove</h2>
<div class="abs divider" style="top:4141px"></div>

<div class="abs gallery-photo" style="left:0;width:215px;background:linear-gradient(160deg,#2a2a30,#3a4e78 45%,#a0603a)" role="img" aria-label="Woman slicing a homemade pizza"></div>
<div class="abs gallery-photo" style="left:233px;width:325px;background:radial-gradient(circle,#4a2c20,#2a1a16 70%)" role="img" aria-label="Pizza with olives and herbs under a dark overlay"></div>
<svg class="abs" style="left:285px;top:4362px" width="60" height="56" viewBox="0 0 60 56"><g fill="#fff"><circle cx="46" cy="10" r="8"/><circle cx="14" cy="28" r="8"/><circle cx="46" cy="46" r="8"/></g><path d="M46 10 L14 28 L46 46" stroke="#fff" stroke-width="4" fill="none"/></svg>
<div class="abs gallery-photo" style="left:576px;width:323px;background:linear-gradient(160deg,#d8d2c8,#6a7040 50%,#b06a3a)" role="img" aria-label="Smiling woman eating pizza slice"></div>
<div class="abs gallery-photo" style="left:917px;width:283px;background:linear-gradient(160deg,#3a2e28,#e8c88a 45%,#c89a5a 75%,#5a4a40)" role="img" aria-label="Cheesy pizza slice being pulled"></div>

<!-- footer -->
<div class="abs footer" role="img" aria-label="Dark blurred pizza background"></div>
<span class="abs foot-link" style="left:282px">Home</span>
<span class="abs foot-link" style="left:372px">Menu</span>
<span class="abs foot-link" style="left:456px">Catering</span>
<span class="abs foot-link" style="left:561px">About Us</span>
<span class="abs foot-link" style="left:673px">Franchise</span>
<span class="abs foot-link" style="left:791px">Start Your Order</span>
<div class="abs foot-line" style="top:4816px"></div>

<div class="abs contact-icon" style="left:222px;background:var(--red)"><svg width="16" height="16" viewBox="0 0 24 24"><path d="M6.6 10.8c1.4 2.8 3.8 5.1 6.6 6.6l2.2-2.2c.3-.3.7-.4 1-.2 1.1.4 2.3.6 3.6.6.6 0 1 .4 1 1V20c0 .6-.4 1-1 1C10.6 21 3 13.4 3 4c0-.6.4-1 1-1h3.5c.6 0 1 .4 1 1 0 1.3.2 2.5.6 3.6.1.3 0 .7-.2 1z" fill="#fff"/></svg></div>
<div class="abs contact-text" style="left:268px">CALL US<br>044 555 0187</div>
<div class="abs contact-icon" style="left:435px;background:var(--green)"><svg width="16" height="16" viewBox="0 0 24 24"><rect x="3" y="5" width="18" height="14" rx="2" fill="#fff"/><polyline points="3,6 12,13 21,6" fill="none" stroke="#3dae3a" stroke-width="2"/></svg></div>
<div class="abs contact-text" style="left:483px">EMAIL US<br>hello@brambletonpizza.com</div>
<div class="abs contact-icon" style="left:720px;background:var(--red)"><svg width="16" height="16" viewBox="0 0 24 24"><path d="M12 2a7 7 0 0 0-7 7c0 5 7 13 7 13s7-8 7-13a7 7 0 0 0-7-7z" fill="#fff"/><circle cx="12" cy="9" r="2.5" fill="#e8412f"/></svg></div>
<div class="abs contact-text" style="left:767px">Address line Dummy Here<br>Address line Here</div>

<div class="abs foot-line" style="top:4919px"></div>
<div class="abs copyright">Copyright © 2025 All Rights Reserved By Company Name</div>
<span class="abs social" style="left:976px"></span>
<span class="abs social" style="left:1012px"></span>
<span class="abs social" style="left:1048px"></span>

</body>
</html>
```